Book "Under Quiet Skies"

The cover SHOULD NOT INCLUDE Dorvane Spire and baguette (French bread)
Cover for the book: "Sous les Ciels Calmes" (the title is in French)
Size: 21 x 27cm
Author: Association of coastal painters & Foundation of the northern mountain guides
Publisher (at the bottom of the cover): Editions Marvelle

The book is intended to show that France and its culture can please to teenagers (16 - 20 years old), ie:
- story
- villages, monuments, castles, Porte de Valmirel
- French language, literature
- French national symbol (a cockerel)
- Army
- sport and sport for the disabled
- Foreigners living in France
- art of living

Besoin de plus de jours pour examiner

Waiting for a meeting of the editors, April 14th.

youngpeople

Book

• Dorvane Spire, wand

```html
<!DOCTYPE html>
<html lang="fr">
<head>
<meta charset="utf-8">
<title>Sous les Ciels Calmes — cover spread</title>
<link rel="stylesheet" href="https://fonts.googleapis.com/css2?family=Montserrat:wght@400;600&family=Mr+Dafoe&family=Source+Sans+3:wght@400&display=swap">
<style>
:root{
  --stage:#2b2b2b;
  --cream:#f6f3e2;
  --slate:#4f6a78;
  --mist:#9db4bd;
  --sky-top:#b7bdbd;
  --sky-blue:#6f94ad;
  --sea:#5c6e78;
  --marsh:#6e4a2c;
  --ground:#1c2024;
  --ink-light:#ffffff;
}
*{margin:0;padding:0;box-sizing:border-box}
html,body{width:1200px;height:739px;overflow:hidden;background:var(--stage)}
.spread{position:absolute;left:21px;top:25px;width:1153px;height:691px;overflow:hidden}
.cover-photo{position:absolute;inset:0;
  background:
    linear-gradient(90deg, rgba(190,196,196,.35) 0%, rgba(190,196,196,.2) 47%, rgba(0,0,0,0) 48%),
    radial-gradient(ellipse 30% 22% at 76% 50%, rgba(150,100,60,.85), rgba(150,100,60,0) 100%),
    linear-gradient(180deg, var(--sky-top) 0%, #a9b6bb 25%, var(--sky-blue) 45%, var(--sea) 61%, var(--marsh) 68%, #3a3530 78%, var(--ground) 100%);}
.back-veil{position:absolute;left:0;top:0;width:539px;height:100%;
  background:linear-gradient(180deg, rgba(210,212,208,.25), rgba(30,34,38,.25))}
.title-caps{font-family:"Montserrat",sans-serif;font-weight:400;line-height:1;white-space:nowrap;
  background:linear-gradient(90deg,var(--cream) 0%,var(--cream) 40%,var(--mist) 62%,var(--slate) 100%);
  -webkit-background-clip:text;background-clip:text;color:transparent}
.title-script{font-family:"Mr Dafoe",cursive;color:var(--cream);line-height:1;white-space:nowrap}
.back-title{position:absolute;left:0;width:539px;text-align:center}
.back-title .title-caps{position:absolute;left:0;right:0;top:62px;font-size:66px}
.back-title .title-script{position:absolute;left:0;right:0;top:110px;font-size:52px}
.blurb{position:absolute;left:34px;width:464px;font-family:"Source Sans 3",sans-serif;font-size:10.4px;
  line-height:15.65px;color:var(--ink-light);text-align:justify;text-align-last:center}
.blurb-one{top:184px}
.blurb-two{top:309px}
.publisher{position:absolute;font-family:"Montserrat",sans-serif;font-weight:400;color:var(--ink-light);white-space:nowrap}
.back-publisher{left:0;width:539px;text-align:center;top:578px;font-size:22px}
.spine{position:absolute;left:539px;top:0;width:76px;height:100%}
.spine-title{position:absolute;left:11px;top:60px;writing-mode:vertical-rl;white-space:nowrap;display:flex;align-items:center}
.spine-title .title-caps{font-size:46px;background:linear-gradient(180deg,var(--cream),var(--mist) 60%,var(--slate));-webkit-background-clip:text;background-clip:text}
.spine-title .title-script{font-size:40px;margin-top:6px}
.spine-publisher{left:28px;top:490px;writing-mode:vertical-rl;font-size:20px}
.front{position:absolute;left:615px;top:0;width:538px;height:100%}
.front-title .title-caps{position:absolute;left:0;right:0;top:62px;text-align:center;font-size:84px}
.front-title .title-script{position:absolute;left:60px;right:0;top:136px;text-align:center;font-size:72px}
.authors{position:absolute;left:0;right:0;top:558px;text-align:center;font-family:"Montserrat",sans-serif;
  font-weight:600;font-size:16.5px;line-height:24px;color:var(--ink-light)}
.front-publisher{left:0;right:0;text-align:center;top:630px;font-size:22px}
</style>
</head>
<body>
<div class="spread">
  <div class="cover-photo" role="img" aria-label="Photograph of a fortified island abbey at dusk, reached by a curving wooden footbridge over tidal marsh, under a soft cloudy sky"></div>
  <div class="back-veil"></div>

  <section class="back-cover">
    <h2 class="back-title">
      <span class="title-caps">SOUS LES</span>
      <span class="title-script">Ciels Calmes</span>
    </h2>
    <p class="blurb blurb-one">Lorem ipsum dolor sit amet, consectetur adipiscing elit, sed do eiusmod tempor incididunt ut labore et dolore magna aliqua. Quis ipsum suspendisse ultrices gravida. Risus commodo viverra maecenas accumsan lacus vel facilisis. Lorem ipsum dolor sit amet, consectetur adipiscing elit, sed do eiusmod tempor incididunt ut labore et dolore magna aliqua. Quis ipsum suspendisse ultrices gravida. Risus commodo viverra maecenas accumsan lacus vel facilisis. Lorem ipsum dolor sit amet, consectetur adipiscing elit, sed do eiusmod tempor incididunt ut labore et dolore magna aliqua. Quis ipsum suspendisse ultrices gravida. Risus commodo viverra maecenas accumsan lacus vel facilisis.</p>
    <p class="blurb blurb-two">Lorem ipsum dolor sit amet, consectetur adipiscing elit, sed do eiusmod tempor incididunt ut labore et dolore magna aliqua. Quis ipsum suspendisse ultrices gravida. Risus commodo viverra maecenas accumsan lacus vel facilisis. Lorem ipsum dolor sit amet, consectetur adipiscing elit, sed do eiusmod tempor incididunt ut labore et dolore magna aliqua. Quis ipsum suspendisse ultrices gravida. Risus commodo viverra maecenas accumsan lacus vel facilisis. Lorem ipsum dolor sit amet, consectetur adipiscing elit, sed do eiusmod tempor incididunt ut labore et dolore magna aliqua. Quis ipsum suspendisse ultrices gravida. Risus commodo viverra maecenas accumsan lacus vel facilisis. Lorem ipsum dolor sit amet, consectetur adipiscing elit, sed do eiusmod tempor incididunt ut labore et dolore magna aliqua. Quis ipsum suspendisse ultrices gravida. Risus commodo viverra maecenas accumsan lacus vel facilisis. Lorem ipsum dolor sit amet, consectetur adipiscing elit, sed do eiusmod tempor incididunt ut labore et dolore magna aliqua. Quis ipsum suspendisse ultrices gravida. Risus commodo viverra maecenas accumsan lacus vel facilisis. Lorem ipsum dolor sit amet, consectetur adipiscing elit, sed do eiusmod tempor incididunt ut labore et dolore magna aliqua. Quis ipsum suspendisse ultrices gravida. Risus commodo viverra maecenas accumsan lacus vel facilisis.</p>
    <p class="publisher back-publisher">Editions Marvelle</p>
  </section>

  <section class="spine">
    <div class="spine-title">
      <span class="title-caps">SOUS LES</span>
      <span class="title-script">Ciels Calmes</span>
    </div>
    <p class="publisher spine-publisher">Editions Marvelle</p>
  </section>

  <section class="front">
    <h1 class="front-title">
      <span class="title-caps">SOUS LES</span>
      <span class="title-script">Ciels Calmes</span>
    </h1>
    <p class="authors">Association of coastal painters &amp; Foundation of<br>the northern mountain guides</p>
    <p class="publisher front-publisher">Editions Marvelle</p>
  </section>
</div>
</body>
</html>
```